Wed site for biomedical device startup

We need a generic website for a medical device startup. I will provide examples below of websites from other companies that can serve as models for what we are looking for. The startup is for a device that can non invasively measure blood flow in the brain using light. The application is to detect the type of stroke someone is having before they get to the hospital so treatment can be started right away. This saves patients upto hours of delayed treatment. Patients will be able to recover from stroke much better and faster as a result. I have attached an AI generated illustration of what the device will ultimately look like for reference.

https://www.372clinicaltech.com
https://vextalune.com

Target Market(s)

Biomedical, medical device, investors of biomedical device startups

Industry/Entity Type

Biomedical

Coding

Coded - Design and coding required

Number of Pages Required

4 page

Requirements
Must have
• same section and section headings as example websites listed above
Nice to have
• similar to example websites listed above. Prefer a darker website over a lighter one. Perhaps dark blues to go with logo colors. A moving background image element at top of landing page could be cool. Something indicative of heartbeat, or neurons, or blood flow.

```html
<!DOCTYPE html>
<html lang="en">
<head>
<meta charset="utf-8">
<title>LUMVIA — Improving the future for the patients</title>
<link rel="stylesheet" href="https://fonts.googleapis.com/css2?family=Lexend:wght@400;500;600&family=Raleway:wght@400;500;600;700&display=swap">
<style>
  :root {
    --bg: #0a0640;
    --bg-deep: #08053a;
    --purple: #6a2bb8;
    --violet: #8a45dc;
    --card-purple: #7b3fd2;
    --cyan: #3fb8e8;
    --accent-text: #4cc3ef;
    --white: #ffffff;
    --line: rgba(255,255,255,0.7);
    --field-line: rgba(255,255,255,0.28);
  }
  * { box-sizing: border-box; margin: 0; padding: 0; }
  html, body { width: 1200px; height: 3233px; overflow: hidden; }
  body {
    position: relative;
    background:
      radial-gradient(ellipse 700px 420px at 0 0, rgba(120,50,200,0.75), transparent 70%),
      var(--bg);
    color: var(--white);
    font-family: "Raleway", sans-serif;
  }
  .abs { position: absolute; }
  .heading { font-family: "Lexend", sans-serif; font-weight: 500; }

  /* decorative background areas */
  .hero-art { left: 0; top: 190px; width: 1200px; height: 420px;
    background: radial-gradient(ellipse 520px 200px at 920px 300px, rgba(70,60,190,0.45), transparent 70%),
                radial-gradient(ellipse 500px 160px at 380px 320px, rgba(110,50,200,0.3), transparent 70%); }
  .partners-art { left: 0; top: 1500px; width: 1200px; height: 380px;
    background: radial-gradient(ellipse 640px 170px at 600px 190px, rgba(60,50,170,0.35), transparent 72%); }
  .footer-art { left: 0; top: 2930px; width: 1200px; height: 303px;
    background: radial-gradient(ellipse 620px 160px at 600px 120px, rgba(80,50,190,0.3), transparent 72%); }

  /* header */
  .brand { display: flex; align-items: center; gap: 8px; font-family: "Lexend", sans-serif; font-weight: 400; font-size: 28px; letter-spacing: 2px; color: var(--white); }
  .brand-dot { width: 38px; height: 38px; border-radius: 50%; background: var(--violet); }
  .site-nav { left: 567px; top: 28px; display: flex; align-items: center; font-size: 16px; }
  .site-nav a { color: var(--white); text-decoration: none; padding: 7px 18px; }
  .site-nav a.is-active { border: 1.5px solid var(--violet); border-radius: 20px; padding: 7px 22px; }

  /* hero */
  .hero-title { left: 0; width: 1200px; top: 255px; text-align: center; font-size: 48px; line-height: 57px; }
  .hero-text { left: 340px; width: 520px; top: 384px; text-align: center; font-size: 13px; line-height: 24px; }
  .btn { display: flex; align-items: center; justify-content: center; border: 1.5px solid var(--violet); border-radius: 26px; font-family: "Lexend", sans-serif; font-weight: 500; font-size: 17px; color: var(--white); }
  .hero-btn { left: 497px; top: 484px; width: 206px; height: 48px; }
  .dots { left: 571px; top: 563px; display: flex; gap: 9px; }
  .dots span { width: 8px; height: 8px; border-radius: 50%; background: var(--violet); }
  .dots span.on { background: var(--white); }

  /* technology */
  .eyebrow { left: 139px; top: 689px; font-size: 12px; font-weight: 600; color: var(--accent-text); }
  .tech-title { left: 138px; top: 705px; font-size: 43px; line-height: 53px; }
  .feature { left: 138px; width: 440px; display: flex; gap: 26px; }
  .feature-icon { flex: none; width: 62px; height: 62px; border-radius: 50%; border: 1.5px solid var(--violet); display: flex; align-items: center; justify-content: center; }
  .feature h3 { font-weight: 700; font-size: 19px; margin: 3px 0 10px; }
  .feature p { font-size: 12.5px; line-height: 15px; }
  .tech-visual { left: 607px; top: 672px; width: 455px; height: 542px; border-radius: 34px;
    background: radial-gradient(circle at 40% 45%, #d9a88a, #a8765d 45%, #5a3e3e 80%, #2b2b3a); }

  /* partners */
  .section-title { left: 0; width: 1200px; text-align: center; font-size: 44px; }
  .section-sub { left: 0; width: 1200px; text-align: center; font-size: 13px; }
  .partner { width: 214px; height: 95px; border: 1.5px solid var(--line); border-radius: 10px; display: flex; flex-direction: column; align-items: center; justify-content: center; color: #a9a6c4; background: rgba(10,6,64,0.35); }
  .partner strong { font-family: "Lexend", sans-serif; font-weight: 500; font-size: 19px; }
  .partner span { font-size: 15px; font-weight: 600; }

  /* press */
  .press-card { width: 286px; border-radius: 12px; overflow: hidden; background: var(--card-purple); }
  .press-card.is-dark { background: var(--bg-deep); border: 1.5px solid #2a2a7a; }
  .press-image { height: 249px; }
  .press-body { padding: 18px 22px 24px; }
  .press-date { font-size: 12px; font-weight: 500; margin-bottom: 10px; }
  .press-headline { font-weight: 700; font-size: 17px; line-height: 21px; }

  /* contact */
  .contact-text { left: 340px; width: 520px; top: 2637px; text-align: center; font-size: 13px; line-height: 20px; }
  .field { height: 36px; border: 1px solid var(--field-line); background: rgba(255,255,255,0.02); font-size: 12px; padding: 11px 12px; }
  .submit-btn { left: 497px; top: 2834px; width: 206px; height: 48px; }

  /* footer */
  .footer-brand { left: 526px; top: 2979px; }
  .footer-nav { left: 0; width: 1200px; top: 3048px; text-align: center; font-size: 17px; }
  .footer-nav a { color: var(--white); text-decoration: none; }
  .social { width: 41px; height: 41px; border-radius: 50%; border: 1.5px solid var(--violet); display: flex; align-items: center; justify-content: center; font-size: 13px; font-weight: 700; }
  .copyright { left: 0; width: 1200px; top: 3170px; text-align: center; font-size: 14px; }
</style>
</head>
<body>

<div class="hero-art abs" role="img" aria-label="Heartbeat line crossing flowing wave lines"></div>
<div class="partners-art abs" role="img" aria-label="Flowing wave lines background"></div>
<div class="footer-art abs" role="img" aria-label="Flowing wave lines background"></div>

<header>
  <div class="brand abs" style="left:138px;top:27px"><span class="brand-dot"></span>LUMVIA</div>
  <nav class="site-nav abs">
    <a class="is-active" href="#">Home</a>
    <a href="#">About Us</a>
    <a href="#">Technology</a>
    <a href="#">Press</a>
    <a href="#">Contact Us</a>
  </nav>
</header>

<section class="hero">
  <h1 class="hero-title heading abs">Improving the future<br>for the patients</h1>
  <p class="hero-text abs">Lorem ipsum dolor sit amet, consectetur adipiscing elit, sed do eiusmod tempor incididunt ut labore et dolore magna aliqua. Quis ipsum suspendisse ultrices gravida. Risus commodo viverra maecenas accumsan lacus vel facilisis.</p>
  <a class="btn hero-btn abs">Connect With Us</a>
  <div class="dots abs"><span></span><span class="on"></span><span></span><span></span></div>
</section>

<section class="technology">
  <p class="eyebrow abs">Advanced Technology</p>
  <h2 class="tech-title heading abs">Innovative Blood<br>Loss Monitoring</h2>

  <div class="feature abs" style="top:845px">
    <div class="feature-icon">
      <svg width="24" height="30" viewBox="0 0 24 30" fill="none" stroke="#fff" stroke-width="2.2"><rect x="4" y="2" width="16" height="26" rx="3"/><line x1="10" y1="23" x2="14" y2="23"/></svg>
    </div>
    <div><h3>Portable Monitoring</h3><p>Lorem ipsum dolor sit amet, consectetur adipiscing elit, sed do eiusmod tempor incididunt ut labore et dolore magna aliqua. facilisis.</p></div>
  </div>
  <div class="feature abs" style="top:966px">
    <div class="feature-icon">
      <svg width="30" height="30" viewBox="0 0 30 30" fill="none" stroke="#fff" stroke-width="2.2"><circle cx="15" cy="15" r="12"/><polyline points="15,8 15,15 20,18"/></svg>
    </div>
    <div><h3>Real-time Alerts</h3><p>Lorem ipsum dolor sit amet, consectetur adipiscing elit, sed do eiusmod tempor incididunt ut labore et dolore magna aliqua. facilisis.</p></div>
  </div>
  <div class="feature abs" style="top:1095px">
    <div class="feature-icon">
      <svg width="32" height="28" viewBox="0 0 32 28" fill="none" stroke="#fff" stroke-width="2"><circle cx="12" cy="9" r="5"/><path d="M3 25c0-5 4-8 9-8s9 3 9 8z"/><line x1="26" y1="6" x2="26" y2="14"/><line x1="22" y1="10" x2="30" y2="10"/></svg>
    </div>
    <div><h3>Patient-Centered</h3><p>Lorem ipsum dolor sit amet, consectetur adipiscing elit, sed do eiusmod tempor incididunt ut labore et dolore magna aliqua. facilisis.</p></div>
  </div>

  <div class="tech-visual abs" role="img" aria-label="Patient wearing forehead light sensors connected to a handheld monitoring device"></div>
</section>

<section class="partners">
  <h2 class="section-title heading abs" style="top:1365px">Partners and Collaborators</h2>
  <p class="section-sub abs" style="top:1432px">Working together with leading institutions to advance medical technology</p>

  <div class="partner abs" style="left:138px;top:1537px"><strong>PARTNERS LOGO</strong><span>Placeholder</span></div>
  <div class="partner abs" style="left:373px;top:1569px"><strong>PARTNERS LOGO</strong><span>Placeholder</span></div>
  <div class="partner abs" style="left:611px;top:1537px"><strong>PARTNERS LOGO</strong><span>Placeholder</span></div>
  <div class="partner abs" style="left:851px;top:1569px"><strong>PARTNERS LOGO</strong><span>Placeholder</span></div>
  <div class="partner abs" style="left:138px;top:1665px"><strong>PARTNERS LOGO</strong><span>Placeholder</span></div>
  <div class="partner abs" style="left:373px;top:1697px"><strong>PARTNERS LOGO</strong><span>Placeholder</span></div>
  <div class="partner abs" style="left:611px;top:1665px"><strong>PARTNERS LOGO</strong><span>Placeholder</span></div>
  <div class="partner abs" style="left:851px;top:1697px"><strong>PARTNERS LOGO</strong><span>Placeholder</span></div>
</section>

<section class="press">
  <h2 class="section-title heading abs" style="top:1927px">Press</h2>
  <p class="section-sub abs" style="top:1993px">Quis ipsum suspendisse ultrices gravida. Risus commodo viverra maecenas</p>

  <article class="press-card abs" style="left:138px;top:2069px">
    <div class="press-image" role="img" aria-label="Doctor showing a tablet to an elderly patient" style="background:linear-gradient(135deg,#c9b9a8,#a07a6a 50%,#d6c2b5)"></div>
    <div class="press-body"><p class="press-date">15.04.25</p><p class="press-headline">Lorem ipsum dolor sit amet consectetur scing elit,enas accumsan lacus vel facilisis.</p></div>
  </article>
  <article class="press-card is-dark abs" style="left:457px;top:2117px">
    <div class="press-image" role="img" aria-label="Glowing brain held above an open hand" style="background:radial-gradient(circle at 50% 40%,#8fd3f2,#3a7fb0 45%,#9fb8cc 90%)"></div>
    <div class="press-body"><p class="press-date">15.04.25</p><p class="press-headline">Lorem ipsum dolor sit amet consectetur scing elit,enas accumsan lacus vel facilisis.</p></div>
  </article>
  <article class="press-card abs" style="left:773px;top:2069px">
    <div class="press-image" role="img" aria-label="Patient resting in a clinic chair wearing a light-based head sensor" style="background:linear-gradient(135deg,#4a5b78,#8a95a8 50%,#3a4560)"></div>
    <div class="press-body"><p class="press-date">15.04.25</p><p class="press-headline">Lorem ipsum dolor sit amet consectetur scing elit,enas accumsan lacus vel facilisis.</p></div>
  </article>
</section>

<section class="contact">
  <h2 class="section-title heading abs" style="top:2576px">Contact Us</h2>
  <p class="contact-text abs">Join our community to receive updates about our latest developments and research in blood loss monitoring technology.</p>
  <div class="field abs" style="left:152px;top:2709px;width:286px">First Name*</div>
  <div class="field abs" style="left:457px;top:2709px;width:286px">Last Name*</div>
  <div class="field abs" style="left:762px;top:2709px;width:286px">Company*</div>
  <div class="field abs" style="left:152px;top:2765px;width:286px">Email*</div>
  <div class="field abs" style="left:457px;top:2765px;width:591px">Messgae</div>
  <a class="btn submit-btn abs">Submit</a>
</section>

<footer>
  <div class="brand footer-brand abs"><span class="brand-dot"></span>LUMVIA</div>
  <nav class="footer-nav abs"><a href="#">Home</a> . <a href="#">About Us</a> . <a href="#">Technology</a> . <a href="#">Press</a> . <a href="#">Contact Us</a></nav>
  <div class="social abs" style="left:522px;top:3096px">f</div>
  <div class="social abs" style="left:579px;top:3096px">x</div>
  <div class="social abs" style="left:636px;top:3096px">
    <svg width="15" height="15" viewBox="0 0 16 16" fill="none" stroke="#fff" stroke-width="1.6"><rect x="2" y="2" width="12" height="12" rx="3.5"/><circle cx="8" cy="8" r="2.8"/></svg>
  </div>
  <p class="copyright abs">© 2025 |&nbsp; www.lumvia.com</p>
</footer>

</body>
</html>
```